Website Comps for Famous Southern BBQ Restaurant in Alabama

We need an authentic, brand-focused redesign for a restaurant.

We need an authentic look.
The client really likes this website.
https://pelmarsmokehouse.example/

I don't want to see a bunch of crazy colors.
Avoid image sliders on the homepage. I hate those.

Please mockup the following three pages:
Homepage
Interior page (for mockup purposes, you can do an About page)
Menu page

I only need the PSD's; not the website coded.

Here is the current website: www.kortiespit.example

https://pelmarsmokehouse.example/

Here are some additional stock photos. New photos will be shot, but these may help for your mock-up designs.
https://files.quillbox.example/sh/83kkqvtrd41zpa7/XQM20PbT9LyRk-wnEuvJ3tpd?dl=0
Updates

I realize we don't have a lot of high-quality photos to work with.Those will be shot.Here are some additional stock photos that may help.https://files.quillbox.example/sh/83kkqvtrd41zpa7/XQM20PbT9LyRk-wnEuvJ3tpd?dl=0 Added Saturday, June 10, 2017

Target Market(s)

United states

Industry/Entity Type

Restaurant

Number of Pages Required

3 page

Font styles to use
Sans Serif

Colors

Designer to choose colors to be used in the design.

Requirements
Must have
• An authentic look.
• The client really likes this website.
• https://pelmarsmokehouse.example/
• It's simple, bold, and vintage at the same time.
• That is what we want.
• Our existing website is
• kortiespit.example
Nice to have
• Simplicity. Something that makes the food look good.
• Possibly a background.
• Logo:
• https://files.quillbox.example/s/t62bnezwhk0qpl3/kories-pit-lakeview.png?dl=0
• Here is a sampling of photos for your comps:
• https://files.quillbox.example/sh/59ryhdupqv2ncmx/MPT4c1ZLvWeQjHoNUyrA8BfxKs?dl=0
Should not have
• Nothing too busy.
• Not too many colors.
• Keep it simple, authentic, "down home."
• No homepage image sliders.

```html
<!DOCTYPE html>
<html lang="en">
<head>
<meta charset="utf-8">
<title>Kortie's Pit – Locations &amp; Contact</title>
<link href="https://fonts.googleapis.com/css2?family=Italianno&family=Source+Sans+3:wght@600;700&family=Open+Sans:wght@400;600;700&display=swap" rel="stylesheet">
<style>
  :root{
    --box:#f7b13f;
    --box-edge:#f0a12a;
    --accent:#f07d22;
    --pin:#e8413f;
    --ink:#111;
    --text:#333;
    --rule:#cfcfcf;
    --map-top:#eef0e6;
    --map-bottom:#e6eadb;
    --brand:#5a1a0e;
  }
  *{margin:0;padding:0;box-sizing:border-box}
  html,body{width:1200px;height:1051px;overflow:hidden;background:#fff}
  body{position:relative;font-family:"Open Sans",sans-serif;color:var(--text)}
  .abs{position:absolute}
  .map{left:0;top:0;width:1200px;height:429px;
    background:linear-gradient(180deg,var(--map-top),var(--map-bottom));}
  .script{font-family:"Italianno",cursive;font-weight:400;color:var(--ink);font-size:54px;width:400px;text-align:center;left:400px;line-height:1}
  .divider{left:499px;width:200px;height:20px}
  .location{width:321px;background:var(--box);opacity:.93;border:1px solid var(--box-edge);
    font-family:"Source Sans 3",sans-serif;font-weight:700;color:#000;padding:18px 0 0 22px}
  .location .addr{font-size:15.5px;line-height:19px;font-weight:600}
  .location .hours{font-size:23.5px;line-height:26px;margin-top:8px}
  .location .hours span{display:block;padding-left:30px}
  .pin{width:30px;height:40px}
  .col-title{font-size:19px;color:#222;font-weight:400}
  .lead{font-size:10px;line-height:18px;width:250px}
  .contact-row{font-size:10px;display:flex;align-items:center;gap:10px;left:158px}
  .contact-row svg{width:18px;height:18px}
  .hours-table{left:454px;top:659px;font-size:10px;border-collapse:collapse}
  .hours-table td{height:27.8px;vertical-align:top;padding-top:1px}
  .hours-table .day{font-weight:700;width:119px;color:#222}
  .gallery{left:754px;top:664px;display:grid;grid-template-columns:repeat(3,89px);grid-auto-rows:50px;gap:3px 4px}
  .gallery div{width:89px;height:50px}
  .footer-rule{left:170px;top:893px;width:857px;height:1px;background:var(--rule)}
  .brand{left:450px;width:300px;top:920px;text-align:center;font-family:"Open Sans",sans-serif;font-weight:700;font-size:24px;color:var(--brand)}
  .footer-text{left:290px;width:620px;top:980px;text-align:center;font-size:12px;line-height:19.5px;color:#333}
</style>
</head>
<body>

<div class="abs map" role="img" aria-label="Regional map showing the three restaurant locations"></div>

<h2 class="abs script" style="top:34px">Our Locations</h2>
<svg class="abs divider" style="top:84px" viewBox="0 0 200 20">
  <line x1="0" y1="11" x2="78" y2="11" stroke="#888" stroke-width="1"/>
  <line x1="122" y1="11" x2="200" y2="11" stroke="#888" stroke-width="1"/>
  <g stroke="var(--accent)" stroke-width="2.4" stroke-linecap="round" fill="none">
    <line x1="92" y1="4" x2="108" y2="19"/><line x1="109" y1="4" x2="93" y2="19"/>
    <line x1="89" y1="1" x2="95" y2="7"/><line x1="112" y1="1" x2="106" y2="7"/>
  </g>
</svg>

<div class="abs location" style="left:83px;top:51px;height:93px;padding-top:18px">
  <div class="addr">2150 Alder Ridge Road, Lakeview AL 35901<br>Phone: (555) 014-2271</div>
  <div class="hours" style="margin-top:4px">Mon - Sat: 11:00 am - 8 pm</div>
</div>
<div class="abs location" style="left:813px;top:104px;height:126px">
  <div class="addr">418 Carrow Ave, Millbrook, AL 35054<br>Phone: (555) 017-3840</div>
  <div class="hours">Mon - Sat: 11:00 am - 8 pm<span>Sun: 11:00 am - 4 pm</span></div>
</div>
<div class="abs location" style="left:527px;top:284px;height:128px">
  <div class="addr">77 Hensley St South, Millbrook, AL 35055<br>Phone: (555) 019-6602</div>
  <div class="hours">Mon - Sat: 11:00 am - 8 pm<span>Sun: 11:00 am - 4 pm</span></div>
</div>

<svg class="abs pin" style="left:229px;top:24px" viewBox="0 0 30 40"><path d="M15 0C6.7 0 0 6.5 0 14.6 0 25 15 40 15 40s15-15 15-25.4C30 6.5 23.3 0 15 0z" fill="var(--pin)"/><circle cx="15" cy="14" r="6" fill="#fff"/></svg>
<svg class="abs pin" style="left:958px;top:77px" viewBox="0 0 30 40"><path d="M15 0C6.7 0 0 6.5 0 14.6 0 25 15 40 15 40s15-15 15-25.4C30 6.5 23.3 0 15 0z" fill="var(--pin)"/><circle cx="15" cy="14" r="6" fill="#fff"/></svg>
<svg class="abs pin" style="left:672px;top:258px" viewBox="0 0 30 40"><path d="M15 0C6.7 0 0 6.5 0 14.6 0 25 15 40 15 40s15-15 15-25.4C30 6.5 23.3 0 15 0z" fill="var(--pin)"/><circle cx="15" cy="14" r="6" fill="#fff"/></svg>

<h2 class="abs script" style="top:480px">Get in touch</h2>
<svg class="abs divider" style="top:530px" viewBox="0 0 200 20">
  <line x1="0" y1="11" x2="78" y2="11" stroke="var(--accent)" stroke-width="1"/>
  <line x1="122" y1="11" x2="200" y2="11" stroke="var(--accent)" stroke-width="1"/>
  <g stroke="var(--accent)" stroke-width="2.4" stroke-linecap="round" fill="none">
    <line x1="92" y1="4" x2="108" y2="19"/><line x1="109" y1="4" x2="93" y2="19"/>
    <line x1="89" y1="1" x2="95" y2="7"/><line x1="112" y1="1" x2="106" y2="7"/>
  </g>
</svg>

<h3 class="abs col-title" style="left:159px;top:618px">Contact us</h3>
<p class="abs lead" style="left:156px;top:657px">Lorem ipsum dolor sit amet, consectetur adipisicing elit. Voluptatum nisi quam magni quos laborum,</p>
<div class="abs contact-row" style="top:720px">
  <svg viewBox="0 0 20 20"><path d="M2 7c0-3 4-4 8-4s8 1 8 4v2h-4V7H6v2H2z" fill="#222"/><path d="M5 10h10l2 7H3z" fill="#222"/><circle cx="10" cy="13.5" r="2" fill="#fff"/></svg>
  <span>+ 1234567890</span>
</div>
<div class="abs contact-row" style="top:757px">
  <svg viewBox="0 0 20 20"><path d="M2 8l8-5 8 5v9H2z" fill="#222"/><path d="M3 9l7 5 7-5" stroke="#fff" stroke-width="1.2" fill="none"/></svg>
  <span>hello@kortiespit.example</span>
</div>
<div class="abs contact-row" style="top:795px">
  <svg viewBox="0 0 20 20"><path d="M10 2L1 10h3v8h4v-5h4v5h4v-8h3z" fill="#222"/></svg>
  <span>1234, Lorem ipsum,1234567890</span>
</div>

<h3 class="abs col-title" style="left:452px;top:618px">Opening hour</h3>
<table class="abs hours-table">
  <tr><td class="day">Lorem</td><td>11AM to 11PM</td></tr>
  <tr><td class="day">Lorem</td><td>11AM to 11PM</td></tr>
  <tr><td class="day">Lorem</td><td>11AM to 11PM</td></tr>
  <tr><td class="day">Lorem</td><td>11AM to 11PM</td></tr>
  <tr><td class="day">Lorem</td><td>11AM to 11PM</td></tr>
  <tr><td class="day">Lorem</td><td>11AM to 11PM</td></tr>
  <tr><td class="day">Lorem</td><td>11AM to 11PM</td></tr>
</table>

<h3 class="abs col-title" style="left:754px;top:618px">Gallery</h3>
<div class="abs gallery">
  <div role="img" aria-label="Fresh vegetables" style="background:linear-gradient(135deg,#e0641c,#9fb34a)"></div>
  <div role="img" aria-label="Pizza" style="background:linear-gradient(135deg,#d9a25a,#b8442a)"></div>
  <div role="img" aria-label="Grilled meat skewers" style="background:linear-gradient(135deg,#3a1c14,#a8321e)"></div>
  <div role="img" aria-label="Tacos" style="background:linear-gradient(135deg,#c63a1f,#e6a04a)"></div>
  <div role="img" aria-label="Fruit and vegetables" style="background:linear-gradient(135deg,#e8c83a,#4a8a2a)"></div>
  <div role="img" aria-label="Bowls of stew" style="background:linear-gradient(135deg,#e8ddd0,#a4502a)"></div>
  <div role="img" aria-label="Burger and fries" style="background:linear-gradient(135deg,#f2cf6a,#b07034)"></div>
  <div role="img" aria-label="Barbecue skewers" style="background:linear-gradient(135deg,#5a1e12,#c2482a)"></div>
  <div role="img" aria-label="Burgers with drink" style="background:linear-gradient(135deg,#f7e9d8,#d7322a)"></div>
</div>

<div class="abs footer-rule"></div>
<div class="abs brand">Kortie's Pit</div>
<p class="abs footer-text">Lorem ipsum dolor sit amet, consectetur adipisicing elit. Voluptatum nisi quam magni quos laborum, dolorum accusamus maiores, iste aspernatur reprehenderit omnis. Odio consectetur itaque</p>

</body>
</html>
```